Eye Catching Business Card for Optometrist

We've recently refreshed our logo and now we need a fresh and bold look for our business cards. We provide progressive ways to improve people's vision and protect their eye health.

Use our new logo as guidance into the colors to use. As far as style goes, I love how bold and eye catching the card is for Lanternfield Studio. Feel free to use your creative judgement.

Tagline: "Clearly the best for your vision."

pertinent info to include:

Dr. Marcus Velbrin
Optometrist

7258 Dunmore Ridge Blvd #215
Brantwell, MO 64172
(555) 382-9017

marc@brantwellfamilyeyecare.example
www.brantwellfamilyeyecare.example

```html
<!DOCTYPE html>
<html lang="en">
<head>
<meta charset="UTF-8">
<title>Brantwell Family Eye Care – Business Card</title>
<link href="https://fonts.googleapis.com/css2?family=Exo+2:wght@400;600;700&display=swap" rel="stylesheet">
<style>
  :root {
    --page-bg: #ece8e3;
    --card-white: #ffffff;
    --brand-red: #c9353e;
    --brand-brown: #7d6a5a;
    --brand-tan: #cbb7a2;
    --ink-dark: #4a4546;
    --ink-light: #ffffff;
  }
  * { box-sizing: border-box; margin: 0; padding: 0; }
  html, body {
    width: 1200px; height: 870px; overflow: hidden;
    background: var(--page-bg);
    font-family: "Exo 2", Arial, sans-serif;
  }
  .canvas {
    width: 1200px; height: 870px;
    display: flex; flex-direction: column;
    align-items: center; justify-content: center; gap: 60px;
  }
  .card {
    width: 630px; height: 360px;
    border-radius: 4px;
    box-shadow: 0 8px 24px rgba(0,0,0,.18);
    position: relative; overflow: hidden;
  }
  /* Front */
  .card-front { background: var(--card-white); }
  .card-front .edge-band {
    position: absolute; right: 0; top: 0; width: 120px; height: 100%;
  }
  .brand {
    position: absolute; left: 70px; top: 50%; transform: translateY(-50%);
    display: flex; align-items: center; gap: 22px;
  }
  .brand-mark {
    width: 70px; height: 70px; background: var(--brand-red); flex: none;
  }
  .brand-name {
    color: var(--brand-red);
    font-weight: 700; font-size: 28px; letter-spacing: 1px;
    text-transform: uppercase; line-height: 1.15;
  }
  .tagline {
    position: absolute; left: 70px; bottom: 48px;
    color: var(--brand-brown); font-size: 16px; font-weight: 400; letter-spacing: .5px;
  }
  /* Back */
  .card-back { background: var(--brand-red); color: var(--ink-light); }
  .card-back .curl {
    position: absolute; left: 0; top: 0; width: 130px; height: 100%;
  }
  .person {
    position: absolute; left: 170px; top: 44px;
  }
  .person-name {
    font-size: 28px; font-weight: 600; letter-spacing: 1.5px; text-transform: uppercase;
    line-height: 1.2;
  }
  .person-role { font-size: 19px; margin-top: 4px; }
  .contact {
    position: absolute; left: 170px; top: 150px;
    list-style: none; font-size: 17px; letter-spacing: .4px;
  }
  .contact li {
    display: flex; align-items: center; gap: 12px; line-height: 1.8;
    white-space: nowrap;
  }
  .contact .address { line-height: 1.35; margin-bottom: 12px; display: block; }
  .contact svg { width: 15px; height: 15px; flex: none; }
</style>
</head>
<body>
<main class="canvas">

  <section class="card card-front" aria-label="Card front">
    <div class="brand">
      <div class="brand-mark"></div>
      <div class="brand-name">Brantwell Family<br>Eye Care</div>
    </div>
    <p class="tagline">Clearly the best for your vision.</p>
    <svg class="edge-band" viewBox="0 0 120 360" preserveAspectRatio="none">
      <path d="M120 0 L60 0 Q10 180 60 360 L120 360 Z" fill="var(--brand-tan)"/>
      <path d="M120 0 L78 0 Q36 180 78 360 L120 360 Z" fill="var(--brand-brown)"/>
    </svg>
  </section>

  <section class="card card-back" aria-label="Card back">
    <svg class="curl" viewBox="0 0 130 360" preserveAspectRatio="none">
      <path d="M0 0 L70 0 Q130 180 70 360 L0 360 Z" fill="var(--brand-brown)"/>
      <path d="M0 0 L58 0 Q116 180 58 360 L0 360 Z" fill="var(--card-white)"/>
    </svg>
    <div class="person">
      <div class="person-name">Dr. Marcus Velbrin</div>
      <div class="person-role">Optometrist</div>
    </div>
    <ul class="contact">
      <li class="address">7258 Dunmore Ridge Blvd #215<br>Brantwell, MO 64172</li>
      <li>(555) 382-9017
        <svg viewBox="0 0 16 16"><path d="M4 1 L6.5 4.5 L5 6 Q6.5 9.5 10 11 L11.5 9.5 L15 12 L13 15 Q5 14 1 3 Z" fill="currentColor"/></svg>
      </li>
      <li>marc@brantwellfamilyeyecare.example
        <svg viewBox="0 0 16 16"><rect x="1" y="3" width="14" height="10" fill="currentColor"/><path d="M1 3 L8 9 L15 3" fill="none" stroke="var(--brand-red)" stroke-width="1.3"/></svg>
      </li>
      <li>www.brantwellfamilyeyecare.example
        <svg viewBox="0 0 16 16"><circle cx="8" cy="8" r="6.5" fill="none" stroke="currentColor" stroke-width="1.3"/><ellipse cx="8" cy="8" rx="3" ry="6.5" fill="none" stroke="currentColor" stroke-width="1.1"/><path d="M1.5 8 H14.5" stroke="currentColor" stroke-width="1.1"/></svg>
      </li>
    </ul>
  </section>

</main>
</body>
</html>
```